Website for a Pittsburgh Musical Production

We are creating a website for a musical stage production. Content and copy is included below. We are targeting production in early 2023.

```html
<!DOCTYPE html>
<html lang="en">
<head>
<meta charset="utf-8">
<title>Hollowmere</title>
<link href="https://fonts.googleapis.com/css2?family=Poppins:wght@600;700&family=Rubik:wght@500;600&family=Nunito+Sans:wght@400;600;700;800&display=swap" rel="stylesheet">
<style>
:root{
  --green:#6a8a43;
  --ink:#1a1a1a;
  --white:#ffffff;
  --text:#3a3a3a;
  --header:#1b1b1b;
  --footer:#1a1a1a;
  --mist:#e4e0de;
  --head-font:'Rubik',sans-serif;
  --body-font:'Nunito Sans',sans-serif;
  --logo-font:'Poppins',sans-serif;
}
*{margin:0;padding:0;box-sizing:border-box}
html,body{width:1200px;height:4666px;overflow:hidden}
body{font-family:var(--body-font);color:var(--text);background:var(--white);position:relative}
section,header,footer{position:absolute;left:0;width:1200px}
.abs{position:absolute}
.btn{position:absolute;background:var(--green);color:var(--white);font-family:var(--body-font);font-weight:800;font-size:13px;letter-spacing:.4px;display:flex;align-items:center;justify-content:center;text-transform:uppercase}
.btn.sm{font-size:10px}
.title{position:absolute;left:0;width:1200px;text-align:center;font-family:var(--head-font);font-weight:600;font-size:26px;text-transform:uppercase}
.rule{position:absolute;left:558px;width:84px;height:2px;background:var(--green)}
.photo{position:absolute}

/* header */
.site-header{top:0;height:88px;background:var(--header)}
.logo{position:absolute;font-family:var(--logo-font);font-weight:700;color:var(--white);font-size:25px}
.nav a{position:absolute;top:37px;color:var(--white);font-size:13px;text-decoration:none;font-family:var(--body-font);font-weight:600}

/* hero */
.hero{top:88px;height:580px;background:radial-gradient(ellipse at 40% 40%,#6b5340 0%,#2c2119 45%,#140f0c 100%)}
.hero-kicker{left:753px;top:160px;color:var(--white);font-family:var(--head-font);font-weight:600;font-size:24px}
.hero-title{left:753px;top:190px;color:var(--white);font-family:var(--head-font);font-weight:600;font-size:48px;letter-spacing:.5px}
.dots{left:563px;top:528px;display:flex;gap:10px;align-items:center}
.dots i{width:6px;height:6px;border-radius:50%;background:var(--white);display:block}
.dots i.on{width:11px;height:11px;background:none;border:2px solid var(--white)}

/* about */
.about{top:668px;height:487px;background:var(--white)}
.about h2{left:645px;top:62px;font-family:var(--head-font);font-weight:600;font-size:26px;color:var(--ink)}
.about .line{left:647px;top:97px;width:84px;height:2px;background:var(--green)}
.about p{left:645px;top:128px;width:430px;font-size:17px;line-height:25.6px;color:var(--text)}

/* events */
.events{top:1155px;height:608px;background:linear-gradient(90deg,#1e2418 0%,#0d0f0b 22%,#000 40%)}
.events .title,.gallery .title,.blog .title{top:47px}
.events .title,.gallery .title{color:var(--white)}
.card{position:absolute;width:294px;background:var(--white)}
.card .pic{height:178px}
.badge{position:absolute;left:30px;top:152px;width:48px;height:52px;background:var(--green);color:var(--white);text-align:center;font-family:var(--head-font)}
.badge b{display:block;font-size:17px;font-weight:600;margin-top:5px}
.badge span{display:block;font-size:9px;font-family:var(--body-font)}
.card h3{position:absolute;left:24px;font-family:var(--body-font);font-weight:800;font-size:13px;color:var(--ink)}
.card p{position:absolute;left:24px;width:240px;font-size:12.5px;line-height:17.5px;color:var(--text)}

/* what we do */
.what{top:1763px;height:647px;background:var(--mist)}
.what .title{top:45px;color:var(--ink)}
.what p{position:absolute;left:310px;width:580px;top:114px;text-align:center;font-size:17px;line-height:25.6px;color:var(--text)}

/* gallery */
.gallery{top:2410px;height:845px;background:radial-gradient(ellipse at 30% 45%,#1d3d85 0%,#10234f 45%,#140f2a 100%)}

/* cta */
.cta{top:3255px;height:521px;background:radial-gradient(ellipse at 50% 60%,#6b5a78 0%,#3a3046 40%,#121522 100%)}
.cta h2{position:absolute;left:0;width:1200px;top:80px;text-align:center;color:var(--white);font-family:var(--head-font);font-weight:500;font-size:27px;line-height:38px;text-transform:uppercase}
.cta p{position:absolute;left:0;width:1200px;top:160px;text-align:center;color:var(--white);font-size:17px;line-height:25px}

/* blog */
.blog{top:3776px;height:536px;background:var(--white)}
.blog .title{top:42px;color:var(--ink)}
.blog .rule{top:87px;background:var(--ink);width:58px;left:571px}
.blog .card{box-shadow:0 0 10px rgba(0,0,0,.12)}

/* footer */
.site-footer{top:4312px;height:354px;background:var(--footer);color:var(--white)}
.col-title{position:absolute;top:52px;font-weight:800;font-size:12px;color:var(--white)}
.menu{position:absolute;left:449px;top:92px;list-style:none;font-size:11px;line-height:20px}
.contact-row{position:absolute;display:flex;gap:10px;font-size:11px;line-height:14px}
.ico{width:24px;height:24px;border-radius:50%;background:var(--white);flex:none;display:flex;align-items:center;justify-content:center}
.copy{position:absolute;left:0;width:1200px;top:302px;text-align:center;font-size:9px;color:#cfcfcf}
</style>
</head>
<body>

<header class="site-header">
  <div class="logo" style="left:132px;top:28px">Hollowmere</div>
  <nav class="nav">
    <a style="left:359px">HOME</a>
    <a style="left:433px">ABOUT US</a>
    <a style="left:537px">PROGRAM AND TICKETS</a>
    <a style="left:727px">OUR OFFER</a>
    <a style="left:842px">GALLERY</a>
    <a style="left:925px">BLOG</a>
    <a style="left:989px">CONTACT US</a>
  </nav>
</header>

<section class="hero" role="img" aria-label="Two ballet dancers performing on a dimly lit theatre stage">
  <div class="abs hero-kicker">WELCOME TO</div>
  <div class="abs hero-title">HOLLOWMERE</div>
  <div class="btn" style="left:761px;top:265px;width:138px;height:46px;font-size:15px">Read More</div>
  <div class="abs dots"><i></i><i></i><i class="on"></i><i></i><i></i></div>
</section>

<section class="about">
  <div class="photo" role="img" aria-label="Singer on stage under blue spotlights" style="left:132px;top:43px;width:472px;height:392px;background:radial-gradient(ellipse at 50% 20%,#5d74d8 0%,#1f2fa0 40%,#08082e 100%)"></div>
  <h2 class="abs">ABOUT US</h2>
  <div class="abs line"></div>
  <p class="abs">There are many variations of passages of Lorem Ipsum available, but the majority have suffered alteration in some form, by injected humour, or randomised words which don't look even slightly believable. If you are going to use a passage of Lorem Ipsum, you need to be sure there isn't anything embarrassing hidden in the middle of text. All the Lorem Ipsum generators on the Internet tend to repeat.</p>
  <div class="btn" style="left:648px;top:368px;width:106px;height:36px;font-size:12px">Read More</div>
</section>

<section class="events">
  <div class="title">Upcoming Events</div>
  <div class="rule" style="top:96px;left:556px"></div>

  <div class="card" style="left:133px;top:148px;height:398px">
    <div class="pic" role="img" aria-label="Opera performer in ornate costume on stage" style="background:linear-gradient(135deg,#2b1410,#7a2a1c 50%,#1a0c0a)"></div>
    <div class="badge"><b>13</b><span>APRIL</span></div>
    <h3 style="top:235px">LOREM IPSUM IS SIMPLY DUMMY</h3>
    <p style="top:262px">Sed ut perspiciatis unde omnis iste natus error sit voluptatem accusa ntium doloremque laudantium, totam rem aperiam.</p>
    <div class="btn sm" style="left:26px;top:345px;width:76px;height:30px">Read More</div>
  </div>
  <div class="card" style="left:453px;top:148px;height:398px">
    <div class="pic" role="img" aria-label="Costumed cast performing a stage scene" style="background:linear-gradient(135deg,#1a1410,#5a4028 50%,#120d0a)"></div>
    <div class="badge"><b>13</b><span>APRIL</span></div>
    <h3 style="top:235px">LOREM IPSUM IS SIMPLY DUMMY</h3>
    <p style="top:262px">Sed ut perspiciatis unde omnis iste natus error sit voluptatem accusa ntium doloremque laudantium, totam rem aperiam.</p>
    <div class="btn sm" style="left:26px;top:345px;width:76px;height:30px">Read More</div>
  </div>
  <div class="card" style="left:777px;top:148px;height:398px">
    <div class="pic" role="img" aria-label="Choir and orchestra on a blue-lit concert stage" style="background:linear-gradient(135deg,#101a48,#3a4aa8 50%,#0c1030)"></div>
    <div class="badge"><b>13</b><span>APRIL</span></div>
    <h3 style="top:235px">LOREM IPSUM IS SIMPLY DUMMY</h3>
    <p style="top:262px">Sed ut perspiciatis unde omnis iste natus error sit voluptatem accusa ntium doloremque laudantium, totam rem aperiam.</p>
    <div class="btn sm" style="left:26px;top:345px;width:76px;height:30px">Read More</div>
  </div>
</section>

<section class="what">
  <div class="title">What We Do</div>
  <div class="rule" style="top:80px;left:565px;width:70px"></div>
  <p>There are many variations of passages of Lorem Ipsum available, but the majority have suffered alteration in some form, by injected humour, or randomised words which don't look even slightly believable.</p>
  <div class="photo" role="img" aria-label="Masked performer and singer in a candlelit stage scene" style="left:172px;top:237px;width:856px;height:362px;background:radial-gradient(ellipse at 60% 50%,#2a4a5e 0%,#142430 50%,#070c10 100%)"></div>
  <div class="btn" style="left:546px;top:222px;width:108px;height:32px;font-size:12px">Read More</div>
</section>

<section class="gallery">
  <div class="title">Gallery</div>
  <div class="rule" style="top:90px;left:570px;width:60px"></div>
  <div class="photo" role="img" aria-label="Opera performer in red costume and jewelled headdress" style="left:133px;top:130px;width:304px;height:292px;background:linear-gradient(135deg,#3a1a10,#b8301c 55%,#4a2410)"></div>
  <div class="photo" role="img" aria-label="White half mask against a dark background" style="left:451px;top:130px;width:304px;height:292px;background:radial-gradient(circle at 55% 45%,#8a8a80 0%,#2a2c24 45%,#0a0b08 100%)"></div>
  <div class="photo" role="img" aria-label="Singer in red gown performing with orchestra" style="left:766px;top:130px;width:304px;height:292px;background:radial-gradient(ellipse at 50% 40%,#d8c070 0%,#8a6a30 45%,#3a2a10 100%)"></div>
  <div class="photo" role="img" aria-label="Performer in red costume breathing fire" style="left:133px;top:430px;width:304px;height:292px;background:radial-gradient(ellipse at 45% 20%,#f0b040 0%,#a03a18 40%,#1a0e10 100%)"></div>
  <div class="photo" role="img" aria-label="Costumed cast singing in a stage scene" style="left:451px;top:430px;width:304px;height:292px;background:linear-gradient(135deg,#2a2018,#6a5438 50%,#1a140e)"></div>
  <div class="photo" role="img" aria-label="Masked performer and singer in a candlelit scene" style="left:766px;top:430px;width:304px;height:292px;background:radial-gradient(ellipse at 55% 55%,#2a4658 0%,#13222e 50%,#060a0e 100%)"></div>
  <div class="btn" style="left:525px;top:779px;width:150px;height:34px;font-size:12px">View All Images</div>
</section>

<section class="cta" role="img" aria-label="Cast performing on a smoky stage with blue lit frames">
  <h2>Lorem ipsum dolor sit amet<br>consectetur adipiscing elit</h2>
  <p>Sed ut perspiciatis unde omnis iste natus error sit<br>voluptatem accusantium doloremque laudantium</p>
  <div class="btn" style="left:545px;top:233px;width:110px;height:34px;font-size:12px">Read More</div>
</section>

<section class="blog">
  <div class="title">Latest Blog</div>
  <div class="rule"></div>

  <div class="card" style="left:133px;top:121px;height:367px">
    <div class="pic" role="img" aria-label="Singer silhouetted under purple stage light" style="background:radial-gradient(ellipse at 50% 30%,#b02aa8 0%,#4a1050 45%,#0e0410 100%)"></div>
    <h3 style="top:212px">LOREM IPSUM IS SIMPLY DUMMY</h3>
    <p style="top:240px">Sed ut perspiciatis unde omnis iste natus error sit voluptatem accusa ntium doloremque.</p>
    <div class="btn sm" style="left:26px;top:318px;width:76px;height:28px">Read More</div>
  </div>
  <div class="card" style="left:453px;top:121px;height:367px">
    <div class="pic" role="img" aria-label="Performers in hats on a blue lit stage" style="background:linear-gradient(180deg,#1a2438,#2a4a78 60%,#0c1220)"></div>
    <h3 style="top:212px">LOREM IPSUM IS SIMPLY DUMMY</h3>
    <p style="top:240px">Sed ut perspiciatis unde omnis iste natus error sit voluptatem accusa ntium doloremque.</p>
    <div class="btn sm" style="left:26px;top:318px;width:76px;height:28px">Read More</div>
  </div>
  <div class="card" style="left:774px;top:121px;height:367px">
    <div class="pic" role="img" aria-label="Figure holding a white mask against a grey wall" style="background:linear-gradient(135deg,#3a3a38,#6a6a66 55%,#2a2a28)"></div>
    <h3 style="top:212px">LOREM IPSUM IS SIMPLY DUMMY</h3>
    <p style="top:240px">Sed ut perspiciatis unde omnis iste natus error sit voluptatem accusa ntium doloremque.</p>
    <div class="btn sm" style="left:26px;top:318px;width:76px;height:28px">Read More</div>
  </div>
</section>

<footer class="site-footer">
  <div class="logo" style="left:145px;top:120px">Hollowmere</div>

  <div class="col-title" style="left:449px">MENU</div>
  <ul class="menu">
    <li>HOME</li><li>ABOUT US</li><li>PROGRAM AND TICKETS</li><li>OUR OFFER</li><li>GALLERY</li><li>BLOG</li><li>CONTACT US</li>
  </ul>

  <div class="col-title" style="left:673px">CONTACT US</div>
  <div class="contact-row" style="left:673px;top:92px">
    <span class="ico"><svg width="10" height="13" viewBox="0 0 10 13"><path d="M5 0a5 5 0 0 0-5 5c0 3.5 5 8 5 8s5-4.5 5-8a5 5 0 0 0-5-5zm0 7a2 2 0 1 1 0-4 2 2 0 0 1 0 4z" fill="#1a1a1a"/></svg></span>
    <span>2150 Larkspur Lane<br>Millbrook, PA 15203</span>
  </div>
  <div class="contact-row" style="left:673px;top:144px">
    <span class="ico"><svg width="12" height="12" viewBox="0 0 12 12"><path d="M3 0l2 3-1.3 1.3a7 7 0 0 0 4 4L9 7l3 2-1 2.5C5 12 0 7 .5 1z" fill="#1a1a1a"/></svg></span>
    <span>Call Us<br>888.888.8888</span>
  </div>
  <div class="contact-row" style="left:673px;top:196px">
    <span class="ico"><svg width="12" height="9" viewBox="0 0 12 9"><rect x=".5" y=".5" width="11" height="8" fill="none" stroke="#1a1a1a"/><path d="M.5.5L6 5l5.5-4.5" fill="none" stroke="#1a1a1a"/></svg></span>
    <span>E mail Us<br>info@hollowmerestage.com</span>
  </div>

  <div class="col-title" style="left:961px">FOLLOW US</div>
  <div class="contact-row" style="left:961px;top:92px"><span class="ico"></span><span>Like us on<br>OUR PAGE</span></div>
  <div class="contact-row" style="left:961px;top:144px"><span class="ico"></span><span>Follow us on<br>OUR FEED</span></div>
  <div class="contact-row" style="left:961px;top:196px"><span class="ico"></span><span>Follow us on<br>OUR NETWORK</span></div>

  <div class="copy">Copyright © 2021 All Rights Reserved</div>
</footer>

</body>
</html>
```